TREVAL BUILDWORKS, LLC Webpage portfolio

I want to create a Website that allows my potential clients to browse my Skilled work via before and after photos. I want the website to enhance the work that I provide and potentially drive new business, or at least solidify my work.
I also do 3D CAD and Modeling of New Spaces and it would be nice to show some of that work from pencil design to 3D modeling, which I feel may help give me more clients.

The website needs to show a solid carpenter/company with the skills to get any project completed.

Types of Jobs - Custom Carpentry & Finishes, Kitchens, Baths, Basements, Decks, Porches, Whole House Renovation - Skilled Craftsmanship (Hardwood Flooring, Floor and Wall Tile) and much more...

Target Market(s)

Residential Home Renovation, Kitchen and Bath Renovation, Home Improvement

Industry/Entity Type

Residential Construction

Number of Pages Required

5+ page

Font styles to use
Sans Serif
Script

Requirements
Must have
• Similar to Plinvo.com, except for Treval Buildworks.
• Must be inviting.
• My Services Offered
• A way to reach me or contact me for estimates with some sort of Screening Questionare.
Nice to have
• Inviting Colors
Should not have
• Not sure at this time

```html
<!DOCTYPE html>
<html lang="en">
<head>
<meta charset="utf-8">
<title>Treval Buildworks</title>
<link href="https://fonts.googleapis.com/css2?family=Roboto:ital,wght@0,300;0,400;0,500;0,700;1,400&display=swap" rel="stylesheet">
<style>
:root{
  --accent:#1f9cd8;
  --navy:#1b5575;
  --navy-deep:#113a56;
  --ink:#222;
  --text:#3d3d3d;
  --muted:#666;
  --soft:#f4f5f7;
  --line:#d9dde2;
  --white:#fff;
}
*{box-sizing:border-box;margin:0;padding:0}
html,body{width:1200px;height:2323px;overflow:hidden}
body{font-family:"Roboto",Arial,sans-serif;color:var(--text);background:var(--white);position:relative}
.abs{position:absolute}
/* hero */
.hero{left:0;top:0;width:1200px;height:543px;background:linear-gradient(160deg,#7d8f72 0%,#9aa88a 35%,#c9c1ac 55%,#6f8563 80%,#4e6a4c 100%)}
.topbar{left:0;top:0;width:1200px;height:68px;border-bottom:1px solid rgba(255,255,255,.35);background:rgba(0,0,0,.08)}
.brand{left:44px;top:22px;display:flex;align-items:center;gap:8px;font-weight:700;font-size:15px;color:var(--navy-deep)}
.brand i{width:18px;height:18px;background:var(--navy-deep);display:block}
.nav{left:370px;top:24px;display:flex;gap:38px;list-style:none}
.nav li{color:var(--white);font-size:15px;font-weight:500;text-transform:uppercase}
.btn-pill{top:16px;height:32px;border-radius:16px;font-size:12.5px;font-weight:500;display:flex;align-items:center;justify-content:center}
.login{left:964px;width:62px;border:1.5px solid var(--white);color:var(--white)}
.quote{left:1033px;width:120px;background:var(--white);color:var(--ink)}
/* mail panel */
.mail-panel{left:802px;top:500px;width:348px;height:292px;background:#f0f1f3}
.mail-panel h3{height:43px;background:linear-gradient(90deg,#165577,#246e94);color:var(--white);font-size:18px;font-weight:500;text-align:center;line-height:43px}
.field{position:absolute;background:var(--white);border:1px solid #c9cdd2;font-size:12px;color:#8a8f95;padding:0 14px;display:flex;align-items:center}
.field.area{align-items:flex-start;padding-top:12px}
.send{position:absolute;background:var(--accent);color:var(--white);font-size:13px;font-weight:500;display:flex;align-items:center;justify-content:center}
/* headings */
.sec-title{font-size:22px;font-weight:500;color:var(--ink);text-align:center}
.sec-title span{color:var(--accent)}
.rule{height:0;border-top:1px dashed var(--accent)}
.welcome-text{left:62px;top:598px;width:680px;font-size:12.6px;line-height:19.5px;text-align:center}
.checks{list-style:none;font-size:12.6px}
.checks li{position:absolute;white-space:nowrap;padding-left:22px}
.checks svg{position:absolute;left:0;top:2px}
/* services */
.services{left:0;top:812px;width:1200px;height:302px;background:var(--soft)}
.card{position:absolute;top:921px;width:253px;height:126px}
.card .photo{width:100%;height:100%}
.card .badge{position:absolute;left:50%;top:-22px;margin-left:-24px;width:48px;height:48px;border-radius:50%;background:var(--navy);display:flex;align-items:center;justify-content:center}
.card .label{position:absolute;left:10px;right:10px;top:103px;height:44px;background:linear-gradient(90deg,#164f70,#236d93);color:var(--white);font-size:14px;font-weight:500;display:flex;align-items:center;justify-content:center}
/* projects */
.shot{position:absolute;top:1197px;width:240px;height:187px}
/* testimonials */
.people{left:0;top:1412px;width:1200px;height:400px;background:var(--soft)}
.quote-box{position:absolute;width:410px;font-size:12.4px;line-height:19.5px;font-style:italic;color:#555}
.quote-box b{display:block;font-style:normal;font-weight:400;color:var(--ink);margin-top:8px}
.quote-box.right-align{text-align:right}
.avatar{position:absolute;width:74px;height:74px;border-radius:50%;background:linear-gradient(150deg,#d9c6b4,#8b6c58)}
/* footer */
.skyline{left:0;top:1800px;width:1200px;height:76px;background:linear-gradient(180deg,rgba(27,85,117,0) 0%,rgba(27,85,117,.55) 60%,#1b5575 100%)}
.footer{left:0;top:1875px;width:1200px;height:448px;background:linear-gradient(180deg,#1b5a7c,#133f5d)}
.footer h4{position:absolute;top:1925px;color:var(--white);font-size:18px;font-weight:500}
.f-text{position:absolute;color:var(--white);font-size:12.6px;line-height:19.5px}
.f-field{position:absolute;background:var(--white);border-radius:2px;font-size:12px;color:#8a8f95;padding:0 14px;display:flex;align-items:center}
.socials{left:52px;top:2146px;display:flex;gap:14px}
.socials i{width:12px;height:12px;border-radius:50%;background:var(--white);display:block}
.map{left:615px;top:1966px;width:253px;height:225px;background:linear-gradient(135deg,#e8e4da,#d5dce4 60%,#c9d6c6)}
.foot-rule{left:52px;top:2255px;width:1096px;border-top:1px solid rgba(255,255,255,.55)}
.copy{top:2284px;color:var(--white);font-size:12px;font-weight:500}
</style>
</head>
<body>

<div class="abs hero" role="img" aria-label="Architectural scale model of houses and trees"></div>
<header class="abs topbar"></header>
<div class="abs brand"><i></i>Treval Buildworks</div>
<ul class="abs nav"><li>Home</li><li>About</li><li>Services</li><li>Gallery</li><li>Contact</li></ul>
<div class="abs btn-pill login">Log In</div>
<div class="abs btn-pill quote">Request a Quote</div>

<section class="abs mail-panel">
  <h3>Feel Free to Mail</h3>
  <div class="field" style="left:10px;top:48px;width:154px;height:34px">Name *</div>
  <div class="field" style="left:184px;top:48px;width:154px;height:34px">Email *</div>
  <div class="field" style="left:10px;top:99px;width:154px;height:34px">Phone Number</div>
  <div class="field" style="left:184px;top:99px;width:154px;height:34px">Subject</div>
  <div class="field area" style="left:10px;top:152px;width:328px;height:65px">Write Your Message Here...</div>
  <div class="send" style="left:106px;top:236px;width:136px;height:32px">SEND MESSAGE</div>
</section>

<h2 class="abs sec-title" style="left:52px;top:546px;width:720px">Welcome to <span>Treval Buildworks</span></h2>
<div class="abs rule" style="left:52px;top:586px;width:721px"></div>
<p class="abs welcome-text">Sed ut perspiciatis unde omnis iste natus error sit voluptatem accusantium doloremque laudantium, totam rem aperiam, eaque ipsa quae ab illo chomu inventore veritatis et quasi architecto beatae vitae dicta sunt explicabo. Nemo enim ipsam voluptatem quia voluptas sit aspernatur aut odit aut fugit, sed quia consequun. Lorem ipsum dolor sit amet, consectetur einem adipiscing elit, sed do eiusmod tempor incididunt ut labore et dolore magna aliqua. Ut enim ad minim veniam, quis nostrud exercitation ullamco laboris nisi ut aliquip ex ea commodo consequat. Duis aute irure dolor in reprehend.</p>
<ul class="checks">
  <li style="left:66px;top:715px"><svg width="13" height="11" viewBox="0 0 13 11"><path d="M1 6l4 4 7-9" fill="none" stroke="#1f9cd8" stroke-width="2.4"/></svg>We help clients communicate with a strategic</li>
  <li style="left:427px;top:715px"><svg width="13" height="11" viewBox="0 0 13 11"><path d="M1 6l4 4 7-9" fill="none" stroke="#1f9cd8" stroke-width="2.4"/></svg>We work hard every day to create products</li>
  <li style="left:66px;top:743px"><svg width="13" height="11" viewBox="0 0 13 11"><path d="M1 6l4 4 7-9" fill="none" stroke="#1f9cd8" stroke-width="2.4"/></svg>We combine the latest thinking with innovative</li>
  <li style="left:427px;top:743px"><svg width="13" height="11" viewBox="0 0 13 11"><path d="M1 6l4 4 7-9" fill="none" stroke="#1f9cd8" stroke-width="2.4"/></svg>We keep it simple and pay attention to strength</li>
</ul>

<section class="abs services"></section>
<h2 class="abs sec-title" style="left:0;top:824px;width:1200px">Our <span>Services</span></h2>
<div class="abs rule" style="left:52px;top:864px;width:1096px"></div>

<div class="card" style="left:52px"><div class="photo" role="img" aria-label="Large renovated family home" style="background:linear-gradient(180deg,#3d7bc8,#8aa3b8 50%,#4c7a3a)"></div><div class="badge"><svg width="22" height="22"><circle cx="11" cy="11" r="5" fill="#fff"/></svg></div><div class="label">Residential Home Renovations</div></div>
<div class="card" style="left:332px"><div class="photo" role="img" aria-label="Renovated kitchen with wooden cabinets" style="background:linear-gradient(160deg,#e7e2d8,#9d7a54 60%,#5e4730)"></div><div class="badge"><svg width="22" height="22"><circle cx="11" cy="11" r="5" fill="#fff"/></svg></div><div class="label">Kitchen Renovations</div></div>
<div class="card" style="left:615px"><div class="photo" role="img" aria-label="Renovated bathroom with tile and vanity" style="background:linear-gradient(160deg,#b19a82,#6e5a4a 55%,#2f2a28)"></div><div class="badge"><svg width="22" height="22"><circle cx="11" cy="11" r="5" fill="#fff"/></svg></div><div class="label">Bath Renovations</div></div>
<div class="card" style="left:894px"><div class="photo" role="img" aria-label="Empty room being painted with ladder" style="background:linear-gradient(160deg,#f0dcc1,#d49b62 60%,#9a6238)"></div><div class="badge"><svg width="22" height="22"><circle cx="11" cy="11" r="5" fill="#fff"/></svg></div><div class="label">Home Improvement</div></div>

<h2 class="abs sec-title" style="left:0;top:1128px;width:1200px">Latest <span>Projects</span></h2>
<div class="abs rule" style="left:52px;top:1167px;width:1096px"></div>
<div class="shot" style="left:0" role="img" aria-label="Finished kitchen interior" style2=""></div>
<div class="shot" style="left:0;background:linear-gradient(160deg,#e9e4dc,#9a7b5c)" role="img" aria-label="Finished kitchen interior"></div>
<div class="shot" style="left:240px;background:linear-gradient(160deg,#6d4b36,#c5a586 55%,#8f6a4e)" role="img" aria-label="Covered porch with wood deck"></div>
<div class="shot" style="left:480px;background:linear-gradient(160deg,#3b2a20,#8a5a35 55%,#2e2420)" role="img" aria-label="Dark wood kitchen with island"></div>
<div class="shot" style="left:720px;background:linear-gradient(180deg,#2f6fd0,#9aa4ac 55%,#6b7a5a)" role="img" aria-label="House exterior with new siding"></div>
<div class="shot" style="left:960px;background:linear-gradient(160deg,#d9d6d0,#9c5f45 60%,#6f7a57)" role="img" aria-label="Front porch with white railing"></div>

<section class="abs people"></section>
<h2 class="abs sec-title" style="left:0;top:1429px;width:1200px">What <span>People Say</span></h2>
<div class="abs rule" style="left:52px;top:1467px;width:1096px"></div>
<div class="abs rule" style="left:52px;top:1625px;width:1096px"></div>
<div class="abs" style="left:600px;top:1512px;height:220px;border-left:1px dashed #aab"></div>

<div class="quote-box right-align" style="left:52px;top:1512px">Duis aute irure dolor in reprehenderit in voluptate velit esse cillum dolore eu fugiat nulla pariatur. Excepteur sint occaecat cupidatat non proident, sunt in culpa qui officia deserunt mollit.<b>Reid Halvorsen, Operations Manager</b></div>
<div class="avatar" style="left:490px;top:1514px" role="img" aria-label="Client portrait"></div>
<div class="avatar" style="left:633px;top:1514px" role="img" aria-label="Client portrait"></div>
<div class="quote-box" style="left:738px;top:1512px">Provident, similique sunt in culpa qui officia deserunt mollitia animi, id est laborum et dolorum fuga. Et harum quidem rerum facilis est et expedita distinctio. Nam libero tempore, cum soluta nobis.<b>Nora Pellam, Creative Designer</b></div>

<div class="quote-box right-align" style="left:52px;top:1650px">Luis aute irure dolor in reprehenderit in piluptate velit esse cillum dolore eu fugiat nulla pariatur. Excepteur sint occaecat cupidatat non proident, sunt in culpa qui officia deserunt mollit.<b>Ivy Calder, Manager</b></div>
<div class="avatar" style="left:490px;top:1652px" role="img" aria-label="Client portrait"></div>
<div class="avatar" style="left:633px;top:1652px" role="img" aria-label="Client portrait"></div>
<div class="quote-box" style="left:738px;top:1650px">At vero eos et accusamus et iusto odio dignissimos ducimus qui blanditiis praesentium voluptatum deleniti atque corrupti quos dolores et quas molestias excepturi sint occaecati asperiores.<b>Owen Marsk, Developer</b></div>

<div class="abs skyline" role="img" aria-label="City skyline and airport silhouette"></div>
<footer class="abs footer"></footer>
<h4 style="left:52px">Contact Us</h4>
<p class="f-text" style="left:52px;top:1966px;width:250px">Please feel free to contact us for any issue. Our staff is available to you from 9AM until 5PM on weekdays.</p>
<p class="f-text" style="left:52px;top:2036px"><b style="font-weight:500">Phone:</b> +1 555 014 27 90</p>
<p class="f-text" style="left:52px;top:2073px"><b style="font-weight:500">Office:</b> Company Address Here</p>
<p class="f-text" style="left:52px;top:2107px"><b style="font-weight:500">Email:</b> hello@trevalbuild.com</p>
<div class="abs socials"><i></i><i></i><i></i><i></i><i></i></div>

<h4 style="left:333px">Feel Free to Mail</h4>
<div class="f-field" style="left:333px;top:1966px;width:118px;height:32px">Name *</div>
<div class="f-field" style="left:469px;top:1966px;width:118px;height:32px">Email *</div>
<div class="f-field" style="left:333px;top:2017px;width:254px;height:32px">Subject</div>
<div class="f-field" style="left:333px;top:2069px;width:254px;height:64px;align-items:flex-start;padding-top:12px">Write Your Message Here...</div>
<div class="send" style="left:333px;top:2153px;width:135px;height:33px;background:#fff;color:#222;border-radius:2px">SEND MESSAGE</div>

<h4 style="left:615px">Headquarters</h4>
<div class="abs map" role="img" aria-label="Street map of the Harbor City headquarters area"></div>

<h4 style="left:896px">About Team</h4>
<p class="f-text" style="left:896px;top:1966px;width:258px">Enim congue blandit. Lorem ipsum dolor sit amet, consectetur adipiscing elit. Quisque consectetur interdum finibus. Vestibulum ante ipsum primis in faucibus orci. luctus et ultrices posuere.</p>
<p class="f-text" style="left:896px;top:2076px;width:258px">Cubilia cras blandit finibus ipsum, id porttitor arcu volutpat a. Integer iaculis erat nec justo malesuada faucibus vel tempus sapien. Vivamus aliquam euismod tristique.</p>

<div class="abs foot-rule"></div>
<p class="abs copy" style="left:52px">Copyright © Treval Buildworks</p>
<p class="abs copy" style="left:540px;width:120px;text-align:center">Treval Buildworks</p>
<p class="abs copy" style="left:1000px;width:148px;text-align:right">All rights reserved</p>

</body>
</html>
```